Systems and Technology Consultants - Website

Design & Build a website for a new company which operates in the Systems and Technology space for Transportation, Government and Commercial sectors.

Overall design should be minimalist in nature.
Should also have a feed that provides news and event updates on the main page.
Logo has already been awarded and should be incorporated into the site.

We like the overall layout, functionality and simplicity of the below sites. Submitted designs could be similar to or a combination of the aspects on these sites, or perhaps a whole different concept - we are open to new ideas.
Norvique.com
Teblo.it

Update 1 Dated 27 May 2014

All I am moving away from the Teblo.it website and would like it to be more aligned with Norvique.com not only in layout but in functionality. I will be extending the deadline of this design brief for two weeks to incorporate additional requirements and will add addtional funding to the project.

Apologies for not having more information available to provide but with so many submissions its getting confusing.

Thanks Derek

Please note that the brief has been updated and the deadline has been extended.

Important: We will need two language versions of the website, English and Arabic; the website is hosted on HostPelican

Hello All, Thank you for your submissions. We have narrowed it down to the final 6 designers and I just wanted to take a moment and provide a bit of feedback regarding the concepts that we like and the modifications we are looking for. First, let me mention some of the design functions we like. - At the top of the homepage we really like the "region" or "language" tab so that the website can be viewed in both English and Arabic. - We like the homepage to have clear color variation so that the different sections of the homepage are distinct. Additionally, we like the bottom portion of the homepage to be in red. We feel that draws attention to our contact information. Again, we would like the colors to integrate black, gray-scale, red, etc. - Having a search tab at the top of the home page, or integrated into the main image, so that the site is easy to navigate. - We especially like the main image to have the scrolling tabs at the bottom so it is easy to browse the services offered (Consultancy, Solutions Architecture, Masters Systems Integration, Independent Design Review). - In regards to the services offered tab we really like the idea that a few people presented that have the outside of our logo with an icon in the middle of consultancy, solutions, etc., etc. Secondly, as mentioned in our brief we really enjoy the design of norvique site. Specially, we enjoy the strong iconic images they use, the way the tabs at the top scroll easily, and contact us page that generates an email. Lastly, I've included some photos of the concept we have been working on. What we are trying to demonstrate is how our company offers a range of services that are essentially linked together. We provide individual services that when combined present the full service package. We would like this concept to be integrated into the over concept of our website. Please feel free to ask for clarification of any of the above points or contact us if you have any additional questions. We appreciate all of your hard work and are very excited to see the updated designs. Best, Marta Vennick Quelbrant Senior Program Manager marta.vennick@quelbrant-example.com

Industry/Entity Type

Government

Font styles to use
Serif
Sans Serif

Requirements
Must have
• Must work on/adapt to various/mobile devices (responsive)
Must be simple and straightforward
Colors should be in line/matching with logo
2 language versions: English and Arabic (no Thai)
Services should be the first group/row of items after/below the main image
Note: the website will be hosted by hostpelican
Nice to have
• Submit feedback form
What's New section
The banner at the bottom of the site should not be too large; we would like a narrow one more
It would be nice if the header/top banner (with Home, About, etc. tabs) could stay in place as you scroll down (like Norvique and Chatterloop)
We will likely only use one image with a Company slogan on the Home page rather than a carousel of images to rotate through
Should not have
• This is the existing website: http://www.quelbrant-example.org
We do not like the animation, the way the banner icons/titles bounce
Not simple enough, we don't like the functionality or how pages load so slowly
We do not like the logo centered - it should be at the left
The banner and its tabs should not be towards the right, we would like them to be centered, to go all the way across and to be below the logo

```html
<!DOCTYPE html>
<html lang="en">
<head>
<meta charset="utf-8">
<title>Quelbrant International</title>
<link href="https://fonts.googleapis.com/css2?family=Open+Sans:wght@300;400;600;700&display=swap" rel="stylesheet">
<style>
:root{
  --red:#e8262f;
  --red-dark:#c81d25;
  --ink:#2b2b2b;
  --text:#555;
  --muted:#8a8a8a;
  --line:#e3e3e3;
  --page:#f5f5f4;
  --panel:#f3f3f3;
  --navy:#0d2f48;
  --navy-deep:#0a1c2c;
  --dark:#1c1d21;
  --date:#3a3a3a;
}
*{box-sizing:border-box;margin:0;padding:0}
html,body{width:670px;height:1200px;overflow:hidden}
body{background:var(--page);font-family:"Open Sans",Arial,sans-serif;color:var(--text);position:relative}
.topbar{position:absolute;top:7px;right:62px;font-size:7.5px;color:var(--muted);display:flex;gap:12px}
.site{position:absolute;left:50px;top:24px;width:570px;height:1130px;background:#fff;border:1px solid var(--line)}
.header{height:74px;position:relative}
.brand{position:absolute;left:12px;top:22px;display:flex;align-items:center;gap:7px}
.brand-mark{width:22px;height:22px;background:var(--red)}
.brand-name{color:var(--red);font-weight:700;font-size:14px;letter-spacing:1.5px}
.share{position:absolute;right:12px;top:19px;display:flex;align-items:center;gap:5px;font-size:7.5px;color:var(--muted)}
.share-label{margin-right:4px}
.share-dot{width:11px;height:11px;background:#b3b3b3;border-radius:2px}
.search{position:absolute;right:12px;top:42px;width:153px;height:17px;border:1px solid var(--line);background:#f7f7f7;display:flex;justify-content:flex-end}
.search-btn{width:23px;height:100%;background:var(--red)}
.nav{height:24px;background:var(--panel);border-top:1px solid #ececec;border-bottom:1px solid #e6e6e6;display:flex;font-size:8px;color:var(--ink)}
.nav a{color:inherit;text-decoration:none;display:flex;align-items:center;padding:0 18px}
.nav a.active{background:var(--red);color:#fff;padding:0 17px;font-weight:600}
.welcome{height:123px;text-align:center;padding-top:26px}
.welcome h1{font-weight:300;font-size:15px;color:var(--ink)}
.welcome h1 strong{color:var(--red);font-weight:600}
.welcome p{width:425px;margin:7px auto 0;font-size:7.2px;line-height:12.3px;color:#444}
.hero{height:219px;position:relative;background:linear-gradient(90deg,var(--navy) 0%,#123a57 45%,var(--navy-deep) 100%);overflow:hidden}
.hero-art{position:absolute;right:0;top:0;width:290px;height:100%;background:radial-gradient(circle at 55% 50%,#4e9ad0 0%,#1d5a86 30%,#0e2f4a 65%,#0a1b29 100%)}
.hero-copy{position:absolute;left:28px;top:71px;width:250px;color:#fff;font-size:12.5px;line-height:16px;font-weight:300}
.hero-copy strong{font-weight:700}
.btn{display:inline-block;margin-top:21px;background:var(--red);color:#fff;font-size:7.5px;padding:6px 13px;border-radius:2px;box-shadow:0 1px 0 var(--red-dark)}
.services{padding:0 12px}
.section-rule{display:flex;align-items:center;gap:12px;margin-top:23px;font-size:11px;font-weight:600;color:var(--ink)}
.section-rule::before,.section-rule::after{content:"";flex:1;height:1px;background:var(--line)}
.service-grid{display:grid;grid-template-columns:192px 190px 166px;row-gap:23px;margin-top:24px}
.service h3{font-size:10px;font-weight:400;color:var(--ink);display:flex;align-items:center;gap:6px}
.service h3 svg{width:12px;height:12px;flex:none}
.service p{font-size:6.8px;line-height:12px;color:var(--muted);margin-top:2px;width:166px}
.lower{display:flex;justify-content:space-between;padding:0 12px;margin-top:32px}
.articles{width:259px}
.col-title{font-size:10.5px;font-weight:600;color:var(--ink);margin-bottom:9px}
.acc{display:flex;background:var(--panel);margin-bottom:6px}
.acc-toggle{width:22px;flex:none;display:flex;align-items:flex-start;justify-content:center;background:var(--date);color:#fff;font-size:13px;line-height:22px;height:22px}
.acc.open .acc-toggle{background:var(--red);height:auto}
.acc.open{background:var(--panel)}
.acc.open .rail{width:22px;background:#d4d4d4;flex:none}
.acc-body{padding:5px 8px;font-size:7.5px;color:var(--ink);display:flex;align-items:center}
.acc.open .acc-body{display:block;padding:10px 9px 12px}
.acc.open h4{font-size:9px;font-weight:400;line-height:11px;color:var(--ink)}
.acc.open p{font-size:6.8px;line-height:11px;color:var(--muted);margin-top:7px}
.acc-left{display:flex;flex-direction:column;width:22px;flex:none}
.acc-left .acc-toggle{height:32px;line-height:30px}
.acc-left .rail{flex:1;background:#d4d4d4}
.news{width:230px}
.news-item{display:flex;gap:8px;margin-bottom:13px}
.date{width:34px;flex:none;text-align:center;color:#fff}
.date .day{background:var(--date);font-size:13px;line-height:17px}
.date .mon{background:var(--red);font-size:11px;line-height:15px}
.news-item h4{font-size:9px;font-weight:400;color:var(--ink)}
.news-item p{font-size:6.8px;line-height:11px;color:var(--muted);margin-top:3px}
.footer{position:absolute;left:0;top:906px;width:570px;height:188px;background:radial-gradient(ellipse at 55% 40%,#2a2c31 0%,var(--dark) 70%)}
.portrait{position:absolute;left:12px;top:22px;width:132px;height:166px;background:linear-gradient(180deg,#3a3330 0%,#26262a 100%);border-radius:60px 60px 0 0}
.about{position:absolute;left:150px;top:40px;width:183px;text-align:right;color:#fff}
.about h3{font-size:10px;font-weight:600;margin-bottom:9px}
.about p{font-size:7.2px;line-height:12.3px}
.skills{position:absolute;left:368px;top:40px;width:190px}
.skills h3{font-size:10px;font-weight:600;color:#fff;margin-bottom:8px}
.bar{height:12px;background:#fff;border-radius:6px;margin-bottom:12px;overflow:hidden}
.bar span{display:block;height:100%;background:var(--red);border-radius:6px;color:#fff;font-size:7.2px;line-height:12px;padding-left:9px}
.bottombar{position:absolute;left:0;top:1094px;width:570px;height:36px;display:flex;justify-content:space-between;align-items:center;padding:0 12px;font-size:7.2px;color:var(--muted)}
.crumbs a{color:var(--muted);text-decoration:none}
.crumbs a.active{color:var(--red)}
.crumbs i{font-style:normal;margin:0 3px}
.copyright{color:var(--ink)}
</style>
</head>
<body>
<div class="topbar"><span>Phone: +100 555 0142</span><span>Email: info@quelbrant-example.com</span></div>

<div class="site">
  <header class="header">
    <div class="brand"><span class="brand-mark"></span><span class="brand-name">QUELBRANT</span></div>
    <div class="share"><span class="share-label">Feel like sharing? We won't bite.</span><span class="share-dot"></span><span class="share-dot"></span><span class="share-dot"></span><span class="share-dot"></span></div>
    <div class="search"><span class="search-btn"></span></div>
  </header>

  <nav class="nav">
    <a class="active" href="#">HOME</a><a href="#">Business Units</a><a href="#">Services</a><a href="#">About Us</a><a href="#">Locations</a><a href="#">Contact Us</a>
  </nav>

  <section class="welcome">
    <h1>Welcome To <strong>QUELBRANT International</strong></h1>
    <p>Quelbrant specializes in delivering quality professional services and technical projects that support larger business goals. systems are tools that support a greater business function and need. we understand that most technical projects are conceptualized to support a larger vision with actual business goals in mind and ensure that all of our professional and certified expertise is included in our professional services to meet those goals.</p>
  </section>

  <section class="hero">
    <div class="hero-art" role="img" aria-label="Hand holding a glowing laptop surrounded by network and email icons"></div>
    <div class="hero-copy"><strong>QUELBRANT</strong> Specializes in delivering quality Professional Services and Technical Projects that Supportlarger Business goals.<br><span class="btn">Read More</span></div>
  </section>

  <section class="services">
    <h2 class="section-rule">Our services</h2>
    <div class="service-grid">
      <div class="service"><h3><svg viewBox="0 0 12 12"><rect x="2" y="2" width="8" height="6" fill="none" stroke="#e8262f" stroke-width="1.3"/><rect x="0.5" y="9" width="11" height="1.5" fill="#e8262f"/></svg>Consulting</h3><p>Lorem ipsum dolor sit amet, consectetur adipisicing elit, sed do eiusmod tempor incididunt ut labore et dolore magna aliqua. Ut enim ad minim veniam, quis nostrud exercitation ullamco laboris nisi.</p></div>
      <div class="service"><h3><svg viewBox="0 0 12 12"><circle cx="4" cy="7" r="3" fill="none" stroke="#e8262f" stroke-width="1.8" stroke-dasharray="1.5 1"/><circle cx="9" cy="3" r="2" fill="none" stroke="#e8262f" stroke-width="1.4" stroke-dasharray="1 0.8"/></svg>Engineering</h3><p>Lorem ipsum dolor sit amet, consectetur adipisicing elit, sed do eiusmod tempor incididunt ut labore et dolore magna aliqua. Ut enim ad minim veniam, quis nostrud exercitation ullamco laboris nisi.</p></div>
      <div class="service"><h3><svg viewBox="0 0 12 12"><path d="M2.5 .8h5l2.5 2.5v8H2.5z" fill="none" stroke="#e8262f" stroke-width="1.1"/><path d="M4 6h4M4 8h4" stroke="#e8262f"/></svg>Construction</h3><p>Lorem ipsum dolor sit amet, consectetur adipisicing elit, sed do eiusmod tempor incididunt ut labore et dolore magna aliqua. Ut enim ad minim veniam, quis nostrud exercitation ullamco laboris nisi.</p></div>
      <div class="service"><h3><svg viewBox="0 0 12 12"><path d="M1.5 1h9v5c0 3-4.5 5-4.5 5S1.5 9 1.5 6z" fill="#e8262f"/><path d="M6 2.5h3V6c0 2-3 3.5-3 3.5z" fill="#fff"/></svg>Lorem ipsum dolor</h3><p>Lorem ipsum dolor sit amet, consectetur adipisicing elit, sed do eiusmod tempor incididunt ut labore et dolore magna aliqua. Ut enim ad minim veniam, quis nostrud exercitation ullamco laboris nisi.</p></div>
      <div class="service"><h3><svg viewBox="0 0 12 12"><path d="M6 0L2.5 7h3L4.5 12 9.5 4.5h-3L8 0z" fill="#e8262f"/></svg>Lorem ipsum dolor sit amet</h3><p>Lorem ipsum dolor sit amet, consectetur adipisicing elit, sed do eiusmod tempor incididunt ut labore et dolore magna aliqua. Ut enim ad minim veniam, quis nostrud exercitation ullamco laboris nisi.</p></div>
      <div class="service"><h3><svg viewBox="0 0 12 12"><circle cx="6" cy="6" r="5.5" fill="#e8262f"/><path d="M3.3 6.2l2 2 3.6-4" fill="none" stroke="#fff" stroke-width="1.5"/></svg>Lorem ipsum dolor sit amet</h3><p>Lorem ipsum dolor sit amet, consectetur adipisicing elit, sed do eiusmod tempor incididunt ut labore et dolore magna aliqua. Ut enim ad minim veniam, quis nostrud exercitation ullamco laboris nisi.</p></div>
    </div>
  </section>

  <section class="lower">
    <div class="articles">
      <h2 class="col-title">Articles</h2>
      <div class="acc open">
        <div class="acc-left"><span class="acc-toggle">&minus;</span><span class="rail"></span></div>
        <div class="acc-body"><h4>Lorem ipsum dolor sit amet, consectetur adipisicing elit</h4><p>Lorem Ipsum is simply dummy text of the printing and typesetting industry. Lorem Ipsum has been the industry's standard dummy text ever since the 1500s, when an unknown printer took a galley of type and scrambled it to make a type specimen book.</p></div>
      </div>
      <div class="acc"><span class="acc-toggle">+</span><div class="acc-body">Lorem ipsum dolor sit amet, consectetur adipisicing elit</div></div>
      <div class="acc"><span class="acc-toggle">+</span><div class="acc-body">Lorem ipsum dolor sit amet,</div></div>
    </div>
    <div class="news">
      <h2 class="col-title">News</h2>
      <div class="news-item"><div class="date"><div class="day">27</div><div class="mon">Feb</div></div><div><h4>Lorem ipsum dolor sit amet,</h4><p>Lorem Ipsum is simply dummy text of the printing and typesetting industry</p></div></div>
      <div class="news-item"><div class="date"><div class="day">23</div><div class="mon">Feb</div></div><div><h4>Lorem ipsum dolor sit amet,</h4><p>Lorem Ipsum is simply dummy text of the printing and typesetting industry.</p></div></div>
      <div class="news-item"><div class="date"><div class="day">22</div><div class="mon">Feb</div></div><div><h4>Lorem ipsum dolor sit amet,</h4><p>Lorem Ipsum is simply dummy text of the printing and typesetting industry. Lorem Ipsum has been the industry's standard dummy text</p></div></div>
    </div>
  </section>

  <footer class="footer">
    <div class="portrait" role="img" aria-label="Portrait of a smiling businesswoman with arms crossed"></div>
    <div class="about"><h3>About Us</h3><p>Lorem ipsum dolor sit amet, consectetur adipisicing elit, sed do eiusmod tempor incididunt ut labore et dolore magna aliqua. Ut enim ad minim veniam, quis nostrud exercitation ullamco laboris nisi ut aliquip ex ea commodo consequat. Duis aute irure dolor in voluptate velit esse cillum dolore fugiat nulla Excepteur sint occaecat cupidatat non.</p></div>
    <div class="skills">
      <h3>Services</h3>
      <div class="bar"><span style="width:85%">Construction</span></div>
      <div class="bar"><span style="width:73%">Engineering</span></div>
      <div class="bar"><span style="width:85%">Consulting</span></div>
      <div class="bar"><span style="width:59%">Operations</span></div>
    </div>
  </footer>

  <div class="bottombar">
    <div class="crumbs"><a class="active" href="#">HOME</a><i>/</i><a href="#">Business Units</a><i>/</i><a href="#">Services</a><i>/</i><a href="#">About Us</a><i>/</i><a href="#">Locations</a><i>/</i><a href="#">Contact Us</a></div>
    <div class="copyright">Copyright © 2014 Quelbrant . All rights reserved.</div>
  </div>
</div>
</body>
</html>
```